Stationary design for boutique production house

We need a stationary design for our production house, 'Lorno Productions' based in Singapore. We produce microfilms as well as podcasts, talkshows and events. Our logo is a stylized icon of our director, who is also the executive producer and host of our programs, Lorno. Our main company colors are Red, Black and white. We would like a clean, minimalist design incorporating our existing company logo that conveys a sense of urbanism and elegance.

Logo and font files are attached. f

Target Market(s)

We focus on lifestyle media rather than entertainment.

Industry/Entity Type

Boutique

Font styles to use
Serif
Sans Serif

Colors
ec1f27
ffffff
000000

Requirements
Must have
• Our company logo and at least one of our company colors.
Nice to have
• Our address and contact information.
Should not have
• Changes made to the company logo (using only certain parts of it is fine though)

```html
<!DOCTYPE html>
<html lang="en">
<head>
<meta charset="UTF-8">
<title>Lorno Productions — Business Card</title>
<link rel="stylesheet" href="https://fonts.googleapis.com/css2?family=Jost:wght@400;500&display=swap">
<style>
  :root {
    --backdrop: #3a3a3a;
    --card-front: #f7f7f6;
    --card-back: #231f20;
    --red: #ec1f27;
    --ink: #1e1b1c;
    --text: #3b3b3b;
    --white: #ffffff;
    --divider: #c9c9c9;
  }
  * { margin: 0; padding: 0; box-sizing: border-box; }
  html, body {
    width: 1200px; height: 768px; overflow: hidden;
    background: var(--backdrop);
    font-family: "Jost", "Helvetica Neue", Arial, sans-serif;
  }
  .card {
    position: absolute; top: 224px;
    width: 555px; height: 320px;
    border-radius: 18px;
  }
  .card-back { left: 30px; background: var(--card-back); }
  .card-front { left: 615px; background: var(--card-front); }
  .card-frame {
    position: absolute; inset: 12px;
    border: 1.5px solid var(--red);
    border-radius: 13px;
  }

  /* Reverse side */
  .back-brand {
    position: absolute; left: 0; right: 0; top: 0; bottom: 40px;
    display: flex; flex-direction: column; align-items: center; justify-content: center;
    gap: 14px;
  }
  .back-brand .brand-name { color: var(--white); font-size: 30px; }
  .back-web {
    position: absolute; left: 0; right: 0; bottom: 34px;
    text-align: center; color: var(--white);
    font-size: 11px; letter-spacing: 4px;
  }

  /* Shared brand lockup */
  .brand-dot { width: 16px; height: 16px; border-radius: 50%; background: var(--red); }
  .brand-name {
    font-weight: 500; letter-spacing: 1.5px; text-transform: uppercase;
    text-align: center; line-height: 1.1;
  }

  /* Front side */
  .front-brand {
    position: absolute; left: 30px; top: 0; bottom: 0; width: 240px;
    display: flex; flex-direction: column; align-items: center; justify-content: center;
    gap: 12px;
  }
  .front-brand .brand-dot { width: 14px; height: 14px; }
  .front-brand .brand-name { color: var(--ink); font-size: 22px; }
  .divider {
    position: absolute; left: 288px; top: 72px; width: 1px; height: 176px;
    background: var(--divider);
  }
  .details { position: absolute; left: 312px; top: 72px; color: var(--text); }
  .person-name { font-size: 20px; color: var(--ink); letter-spacing: .5px; line-height: 1.15; }
  .person-role { font-size: 15px; color: var(--red); letter-spacing: .5px; margin-bottom: 12px; }
  .address { font-size: 13px; line-height: 1.3; margin-bottom: 8px; }
  .contacts { list-style: none; font-size: 13px; line-height: 1.5; }
  .contacts li { display: flex; align-items: center; gap: 9px; }
  .contacts .icon { width: 12px; height: 12px; fill: var(--ink); flex: none; }
</style>
</head>
<body>
  <section class="card card-back">
    <div class="card-frame"></div>
    <div class="back-brand">
      <span class="brand-dot"></span>
      <p class="brand-name">Lorno<br>Productions</p>
    </div>
    <p class="back-web">www.lornoprod.com</p>
  </section>

  <main class="card card-front">
    <div class="card-frame"></div>

    <section class="front-brand">
      <span class="brand-dot"></span>
      <h1 class="brand-name">Lorno<br>Productions</h1>
    </section>

    <div class="divider"></div>

    <section class="details">
      <p class="person-name">DANIEL REYES</p>
      <p class="person-role">CEO/FOUNDER</p>
      <p class="address">2140 Harbour Street<br>Singapore 048617</p>
      <ul class="contacts">
        <li>
          <svg class="icon" viewBox="0 0 24 24"><path d="M6.6 10.8a15.1 15.1 0 0 0 6.6 6.6l2.2-2.2c.3-.3.7-.4 1-.2 1.1.4 2.3.6 3.6.6.6 0 1 .4 1 1V20c0 .6-.4 1-1 1A17 17 0 0 1 3 4c0-.6.4-1 1-1h3.5c.6 0 1 .4 1 1 0 1.3.2 2.5.6 3.6.1.3 0 .7-.2 1z"/></svg>
          612 555 0148
        </li>
        <li>
          <svg class="icon" viewBox="0 0 24 24"><path d="M7 1h10a2 2 0 0 1 2 2v18a2 2 0 0 1-2 2H7a2 2 0 0 1-2-2V3a2 2 0 0 1 2-2zm0 3v15h10V4z"/></svg>
          618 555 0192
        </li>
        <li>
          <svg class="icon" viewBox="0 0 24 24"><path d="M6 2h10l2 2v5H6zM3 10h18a1 1 0 0 1 1 1v8a1 1 0 0 1-1 1H3a1 1 0 0 1-1-1v-8a1 1 0 0 1 1-1zm4 6v2h10v-2z"/></svg>
          614 555 0177
        </li>
        <li>
          <svg class="icon" viewBox="0 0 24 24"><path d="M2 5h20v14H2zm2 2v.5l8 5 8-5V7l-8 5z"/></svg>
          hello@lornoprod.com
        </li>
        <li>
          <svg class="icon" viewBox="0 0 24 24"><circle cx="12" cy="12" r="10"/><path d="M2 12h20M12 2c3 3 3 17 0 20M12 2c-3 3-3 17 0 20" stroke="#f7f7f6" stroke-width="1.4" fill="none"/></svg>
          www.lornoprod.com
        </li>
      </ul>
    </section>
  </main>
</body>
</html>
```